BRANDEMEIER & BRANDEMEIER,LLP NEEDS A NEW LETTERHEAD DESIGN

a conservative yet contemporary layout befitting a long established
firm, consistent with the times, some form of logo so it catches ones attention, and is
admirable, but portrays integrity
Updates

I would like to approve #22066987 Please advise how to do this as it’s confusing on the site so I can approve payment for the designer

Target Market(s)

real estate investors and building management people

Industry/Entity Type

Law Firm

Font styles to use
Serif

Colors

Designer to choose colors to be used in the design.

Requirements
Must have
• some form of conservative logo

```html
<!DOCTYPE html>
<html lang="en">
<head>
<meta charset="utf-8">
<title>Brandemeier &amp; Brandemeier LLP – Letterhead</title>
<link href="https://fonts.googleapis.com/css2?family=Cinzel:wght@500&family=Lato:wght@400&family=Arimo:wght@400&display=swap" rel="stylesheet">
<style>
  :root {
    --backdrop: #d2d2d2;
    --paper: #f3f3f4;
    --navy: #1c2452;
    --ink: #55565c;
    --rule: #6a6b72;
    --contact-ink: #3b3c42;
  }
  * { margin: 0; padding: 0; box-sizing: border-box; }
  html, body { width: 1200px; height: 994px; overflow: hidden; background: var(--backdrop); }
  .letterhead {
    position: absolute; left: 245px; top: 2px;
    width: 709px; height: 990px;
    background: var(--paper);
    color: var(--ink);
    overflow: hidden;
  }
  .corner-emblem {
    position: absolute; top: 0; right: 0;
    width: 100px; height: 100px;
    background: var(--navy);
  }
  .brand {
    position: absolute; left: 52px; top: 36px; width: 252px;
    text-align: center; color: var(--navy);
  }
  .brand-mark {
    display: block; width: 40px; height: 40px;
    margin: 0 auto 12px;
    background: var(--navy);
  }
  .brand-name {
    font-family: "Cinzel", serif; font-weight: 500;
    font-size: 15.8px; letter-spacing: 0.2px; white-space: nowrap;
    line-height: 18px;
  }
  .brand-suffix {
    display: flex; align-items: center; gap: 8px;
    font-family: "Cinzel", serif; font-weight: 500; font-size: 15.8px;
    line-height: 18px;
  }
  .brand-suffix::before, .brand-suffix::after {
    content: ""; flex: 1; height: 1px; background: var(--rule);
  }
  .letter-body {
    position: absolute; left: 114px; top: 224px; width: 521px;
    font-family: "Lato", sans-serif; font-size: 11.1px; line-height: 18.8px;
  }
  .letter-body p { text-align: justify; margin-bottom: 18.8px; }
  .letter-body .closing { margin-top: 56px; }
  .contact {
    position: absolute; top: 913px;
    font-family: "Arimo", sans-serif; font-size: 11px; line-height: 14.5px;
    color: var(--contact-ink);
  }
  .contact::before {
    content: ""; display: block; width: 18px; height: 3px;
    background: var(--navy); margin-bottom: 16px;
  }
  .contact-phone { left: 58px; }
  .contact-web { left: 270px; }
  .contact-address { left: 495px; }
</style>
</head>
<body>
<main class="letterhead">
  <div class="corner-emblem" role="img" aria-label="Large firm emblem decoration in the top corner"></div>

  <header class="brand">
    <span class="brand-mark" role="img" aria-label="Firm emblem"></span>
    <div class="brand-name">Brandemeier &amp; Brandemeier</div>
    <div class="brand-suffix">LLP</div>
  </header>

  <section class="letter-body">
    <p class="salutation">Dear Daniel Harwood,</p>
    <p>Lorem ipsum dolor sit amet, consectetuer adipiscing elit, sed diam nonummy nibh euismod tincidunt ut laoreet dolore magna aliquam erat volutpat. Ut wisi enim ad minim veniam, quis nostrud exerci tation ullamcorper suscipit lobortis nisl ut aliquip ex ea commodo consequat. Duis dolore te feugait nulla facilisi. Nam liber tempor cum soluta nobis eleifend option congue nihil imperdiet doming id quod mazim placerat facer possim assum. Lorem ipsum dolor sit amet, consectetuer adipiscing elit, sed diam nonummy nibh euismod tincidunt ut laoreet dolore magna aliquam erat volutpat. Ut wisi enim ad minim veniam, quis nostrud exerci tation ullamcorper suscipit lobortis nisl ut aliquip ex ea commodo consequat.</p>
    <p>Consectetuer adipiscing elit, sed diam nonummy nibh euismod tincidunt ut laoreet dolore magna aliquam erat volutpat. Ut wisi enim ad minim veniam, quis nostrud exerci tation ullamcorper suscipit lobortis nisl ut aliquip ex ea commodo consequat. Consectetuer adipiscing elit, sed diam nonummy nibh euismod tincidunt ut laoreet dolore magna aliquam erat volutpat. Ut wisi enim ad minim veniam, quis nostrud exerci tation ullamcorper suscipit lobortis nisl ut aliquip ex ea commodo consequat.</p>
    <p>Consectetuer adipiscing elit, sed diam nonummy nibh euismod tincidunt ut laoreet dolore magna aliquam erat volutpat. Ut wisi enim ad minim veniam, quis nostrud exerci tation ullamcorper suscipit lobortis nisl ut aliquip ex ea commodo consequat. Consectetuer adipiscing elit, sed diam nonummy nibh euismod tincidunt ut laoreet dolore magna aliquam erat volutpat. Ut wisi enim ad minim veniam, quis nostrud exerci tation ullamcorper suscipit lobortis nisl ut aliquip ex ea commodo consequat.</p>
    <p class="closing">Sincerely Yours</p>
  </section>

  <footer>
    <div class="contact contact-phone">P. (555) 214-0391<br>F. (555)-214-0392</div>
    <div class="contact contact-web">info@bbrelaw.com<br>www.brandemeierlaw.com</div>
    <div class="contact contact-address">48 Harbor Lane Suite 210<br>Millbrook, New York 12545</div>
  </footer>
</main>
</body>
</html>
```